Business Card for a Creative Technology based HR services company

Our company name is Lumo8, and we build large communities of HR (human resource) and finance personnels through our mobile platform, and we conduct lots of on-line and off-line activities to get everyone constantly connected. Behind all these, we will also provide on-site HR and finance contractors to our clients, plus a host of other HR-related services. No process in our company takes more than 5-steps.
Our company slogan: Shaping Your Tomorrow
Target Market(s)
All human resource (HR) and finance personnels, from new entrants to highly experienced senior professionals.
Industry/Entity Type
Finance
Colors
Designer to choose colors to be used in the design.
Look and feel
Each slider illustrates characteristics of the customer's brand and the style your logo design should communicate.

```html
<!DOCTYPE html>
<html lang="en">
<head>
<meta charset="utf-8">
<title>Lumo8 Business Card</title>
<link rel="stylesheet" href="https://fonts.googleapis.com/css2?family=Jost:wght@400;500;700&family=Marcellus+SC&display=swap">
<style>
  :root {
    --navy: #13305a;
    --navy-soft: #1b3a66;
    --red: #e3232b;
    --paper: #f3f3f4;
    --ink: #4a4d55;
    --rule: #9a9ca2;
    --tagline: #c9d1de;
    --stage: #e6e6e3;
    --white: #ffffff;
  }
  * { margin: 0; padding: 0; box-sizing: border-box; }
  html, body { width: 1200px; height: 900px; overflow: hidden; }
  body {
    background: var(--stage);
    font-family: "Jost", sans-serif;
    position: relative;
  }
  .card {
    position: absolute;
    left: 280px;
    width: 640px;
    height: 366px;
    overflow: hidden;
    box-shadow: 0 6px 18px rgba(0,0,0,0.18);
  }

  /* Front side */
  .card-front { top: 48px; background: var(--navy); }
  .front-watermark {
    position: absolute;
    left: 150px; top: 20px;
    font-weight: 700;
    font-size: 150px;
    line-height: 1;
    color: var(--navy-soft);
    letter-spacing: -2px;
    white-space: nowrap;
  }
  .front-tagline {
    position: absolute;
    left: 48px; top: 186px;
    font-size: 12px;
    letter-spacing: 5px;
    color: var(--tagline);
    text-transform: uppercase;
    white-space: nowrap;
  }
  .front-brand {
    position: absolute;
    right: 64px; bottom: 60px;
    font-weight: 700;
    font-size: 50px;
    line-height: 1;
    color: var(--white);
    letter-spacing: -1px;
  }

  /* Back side */
  .card-back { top: 486px; background: var(--paper); }
  .back-brand {
    position: absolute;
    left: 52px; top: 40px;
    font-weight: 700;
    font-size: 44px;
    line-height: 1;
    color: var(--navy);
    letter-spacing: -1px;
  }
  .back-divider {
    position: absolute;
    left: 0; right: 40px; top: 118px;
    height: 1px;
    background: var(--rule);
  }
  .address {
    position: absolute;
    left: 52px; top: 196px;
    font-size: 11px;
    letter-spacing: 2px;
    line-height: 22px;
    color: var(--ink);
    text-transform: uppercase;
    white-space: nowrap;
  }
  .person {
    position: absolute;
    right: 52px; top: 146px;
    text-align: right;
  }
  .person-name {
    font-family: "Marcellus SC", serif;
    font-size: 22px;
    letter-spacing: 5px;
    color: #2b2d33;
    white-space: nowrap;
  }
  .person-role {
    display: inline-block;
    margin-top: 4px;
    padding-left: 60px;
    padding-top: 4px;
    border-top: 1px solid var(--rule);
    font-family: "Marcellus SC", serif;
    font-size: 14px;
    letter-spacing: 3px;
    color: var(--navy);
  }
  .contacts {
    position: absolute;
    right: 52px; top: 222px;
    list-style: none;
  }
  .contacts li {
    display: flex;
    justify-content: flex-end;
    align-items: center;
    gap: 14px;
    height: 22px;
    font-size: 13px;
    letter-spacing: 2px;
    color: var(--ink);
    white-space: nowrap;
  }
  .contacts svg { width: 14px; height: 14px; flex: none; }
  .band { position: absolute; left: 0; bottom: 0; width: 640px; height: 40px; }
  .website {
    position: absolute;
    left: 52px; bottom: 12px;
    font-size: 12px;
    letter-spacing: 4px;
    color: var(--white);
    white-space: nowrap;
  }
</style>
</head>
<body>

<section class="card card-front" aria-label="Card front">
  <div class="front-watermark" aria-hidden="true">Lumo8</div>
  <p class="front-tagline">Shaping Your Tomorrow</p>
  <div class="front-brand">Lumo8</div>
</section>

<section class="card card-back" aria-label="Card back">
  <div class="back-brand">Lumo8</div>
  <div class="back-divider"></div>

  <p class="address">1280 Harbor Ave. Suite #4<br>Linwood, CA 95731</p>

  <div class="person">
    <div class="person-name">Dan Mercer</div>
    <div class="person-role">CEO</div>
  </div>

  <ul class="contacts">
    <li>555-214-3870
      <svg viewBox="0 0 14 14" fill="none" stroke="var(--red)" stroke-width="1.3" aria-hidden="true"><path d="M2 5c0-2 2-3 5-3s5 1 5 3l-2 1-1-2H5L4 6z"/><rect x="3" y="7" width="8" height="5" rx="1"/></svg>
    </li>
    <li>555-214-6612
      <svg viewBox="0 0 14 14" fill="none" stroke="var(--red)" stroke-width="1.3" aria-hidden="true"><rect x="4" y="1.5" width="6" height="11" rx="1"/><line x1="6" y1="10.5" x2="8" y2="10.5"/></svg>
    </li>
    <li>555-214-9048
      <svg viewBox="0 0 14 14" fill="none" stroke="var(--red)" stroke-width="1.3" aria-hidden="true"><rect x="1.5" y="5" width="11" height="7" rx="1"/><rect x="4" y="2" width="6" height="3"/><line x1="4" y1="8.5" x2="10" y2="8.5"/></svg>
    </li>
    <li>dmercer@lumo8.com
      <svg viewBox="0 0 14 14" fill="none" stroke="var(--red)" stroke-width="1.3" aria-hidden="true"><rect x="1.5" y="3" width="11" height="8"/><path d="M1.5 3l5.5 5 5.5-5"/></svg>
    </li>
  </ul>

  <svg class="band" viewBox="0 0 640 40" preserveAspectRatio="none" aria-hidden="true">
    <polygon points="0,0 282,0 310,40 0,40" fill="var(--navy)"/>
    <rect x="296" y="34" width="344" height="6" fill="var(--red)"/>
  </svg>
  <div class="website">www.lumo8.com</div>
</section>

</body>
</html>
```